Need a new company business card

I am looking for a new company business card. Front and back. With information on it as per below. Card should be professional. Yet clever. Simple. Modern design. Pim card, traditional size. OK with say, all black or all red backside.

Varnholt is an indie, bootstrapped magazine advancing the work of intersectional feminists busting their buts to create a just world through the power of enterprise and innovation.

Varnholt is the home and voice of entrepreneurial feminism and feminist innovators worldwide. Entrepreneurial feminists are people (of all genders) who see inequality as an innovation priority. They work to advance gender equity and/or who strive to integrate and practice feminist principles, pedagogy, values into their innovation and entrepreneurship work.
We are committed to this space being trans and queer inclusive, anti-racist, intersectional, brave, and safe. We welcome all allies. We value learning, edgy but civil discourse and integrative thinking skills.

Target Market(s)

feminists, business owners,

Industry/Entity Type

Publishing Company

Contact Information for Business Card

RD Tolliver
Founder/Publisher
4-237 Ashgrove Lane, Toronto, ON
M4T 2K8
publisher@varnholt.com
416-552-3019
www.varnholt.com

Font styles to use
Serif
Other font styles liked:
• Myriad Pro

Colors
ec1f27
000000
ffffff

Requirements
Must have
• logo
• use red, black white colours only.
Nice to have
• use the compass in pattern or creatively but not too busy please
Should not have
• Should not be too busy. Elegant.

```html
<!DOCTYPE html>
<html lang="en">
<head>
<meta charset="utf-8">
<title>Varnholt Business Card</title>
<link rel="stylesheet" href="https://fonts.googleapis.com/css2?family=Roboto+Condensed:wght@500;700&family=Roboto:wght@400;500;700&display=swap">
<style>
  :root {
    --red: #ec1f27;
    --ink: #2e2e2e;
    --text: #3a3a3a;
    --rule: #9a9a9a;
    --band: #333333;
    --paper: #f4f4f4;
    --white: #ffffff;
    --backdrop: #e6e4e1;
  }
  * { margin: 0; padding: 0; box-sizing: border-box; }
  html, body { width: 1200px; height: 960px; overflow: hidden; }
  body {
    position: relative;
    background: var(--backdrop);
    font-family: "Roboto", Arial, sans-serif;
  }
  .card {
    position: absolute;
    width: 600px;
    height: 342px;
    box-shadow: 0 2px 6px rgba(0,0,0,0.25);
    overflow: hidden;
  }
  .card-front { left: 314px; top: 113px; background: var(--paper); }
  .card-back { left: 312px; top: 472px; background: var(--red); }

  .wordmark {
    position: absolute;
    font-family: "Roboto", Arial, sans-serif;
    font-weight: 700;
    font-size: 78px;
    line-height: 1;
    letter-spacing: -2px;
    white-space: nowrap;
  }
  .card-front .wordmark { right: 36px; top: 62px; color: var(--ink); }

  .holder-name {
    position: absolute; left: 25px; top: 213px;
    font-family: "Roboto Condensed", Arial, sans-serif;
    font-weight: 700; font-size: 20px; color: var(--ink);
  }
  .holder-title {
    position: absolute; left: 25px; top: 237px;
    font-weight: 500; font-size: 15px; color: var(--red);
  }
  .divider {
    position: absolute; left: 25px; top: 257px;
    width: 551px; height: 2px; background: var(--rule);
  }
  .contact-list {
    position: absolute; left: 25px; top: 272px;
    list-style: none; font-size: 14px; color: var(--text); line-height: 19px;
  }
  .contact-list li { display: flex; align-items: center; gap: 8px; }
  .contact-list svg { width: 13px; height: 13px; fill: var(--ink); }
  .address {
    position: absolute; right: 24px; top: 274px;
    font-size: 14px; color: var(--text); line-height: 19px; text-align: right;
    font-style: normal;
  }
  .footer-band { position: absolute; left: 0; bottom: 0; width: 600px; height: 14px; }

  .card-back .pattern-field { position: absolute; inset: 0; background: var(--red); }
  .card-back .wordmark {
    left: 0; width: 600px; text-align: center; top: 132px;
    color: var(--white); font-size: 82px;
  }
</style>
</head>
<body>
  <section class="card card-front" aria-label="Business card front">
    <div class="wordmark">Varnholt</div>

    <div class="holder-name">RD TOLLIVER</div>
    <div class="holder-title">Founder/Publisher</div>
    <div class="divider"></div>

    <ul class="contact-list">
      <li>
        <svg viewBox="0 0 24 24" aria-hidden="true"><path d="M6.6 10.8a15.1 15.1 0 0 0 6.6 6.6l2.2-2.2a1 1 0 0 1 1-.25 11.4 11.4 0 0 0 3.6.57 1 1 0 0 1 1 1V20a1 1 0 0 1-1 1A17 17 0 0 1 3 4a1 1 0 0 1 1-1h3.5a1 1 0 0 1 1 1c0 1.25.2 2.45.57 3.57a1 1 0 0 1-.25 1z"/></svg>
        416-552-3019
      </li>
      <li>
        <svg viewBox="0 0 24 24" aria-hidden="true"><path d="M2 6l10 7 10-7v12H2z"/><path d="M2 5h20l-10 7z"/></svg>
        publisher@varnholt.com
      </li>
    </ul>

    <address class="address">4-237 Ashgrove Lane<br>Toronto, ON, M4T 2K8</address>

    <svg class="footer-band" viewBox="0 0 600 14" aria-hidden="true">
      <polygon points="0,0 393,0 389,14 0,14" fill="var(--band)"/>
      <polygon points="397,0 600,0 600,14 393,14" fill="var(--red)"/>
    </svg>
  </section>

  <section class="card card-back" aria-label="Business card back">
    <div class="pattern-field" role="img" aria-label="Subtle red repeating pattern background"></div>
    <div class="wordmark">Varnholt</div>
  </section>
</body>
</html>
```